Fun A1 2012 family planner using clever typography and block colour

I have been looking for an A1 2012 family planner and I have not been able to find one. Hence I would like help to develop such a planner. I plan to print it on matt paper, portrait orientated. I have attached some reference pictures of our 2011 planner. I like interesting typography, clear clean colours and simple illustration. I need space to write in daily events and need the weeks and days to be clearly delineated from each other. Each day cell needs the date and day in it (please refer to the file uploaded for a visual reference confirming this). Each weekend needs some kind of colour/ typographic delineation. I want a design for a year-at-a-view calendar. I plan to print the planner in Sydney, Australia with brightloomprints.com.au and probably to sell printed copies online. The terms & conditions of this project are that I will own the design concept 100% and in perpetuity worldwide once payment has been made. (NB. The attached Work File in Word contains a rough layout and all months, days and dates all typed up to make for quicker design.)

Target Market(s)

Reasonably well heeled family of 4. 2 parents. 2 kids. 2 pets.

Industry/Entity Type

Events

Requirements
Must have
• The calendar must be portrait (not landscape orientated), A1 size. It will be printed on matt paper by brightloomprints.com.au. It must have months running left to right (Jan-Dec) and day/date cells running top to bottom (refer 2011 planner photos in file uploaded). The day/ date cells must be around 3(w)x2(h)cm - big enough to write daily events in. Weekends must be colour/ typographically delineated. 2012 year must be noted as must "A Pebblegate Inc Project" and web address in fine print bottom left hand left hand corner.
Nice to have
• A Pebblegate Inc logo in bottom left hand corder (perhaps Nimble Owl like: http://www.artmarketly.com/design_submission.aspx?designid=731462). Header/Footer space for customisation (e.g. "Hartono-Quist 2012 Planner" or "XYZ Co 2012 Planner".
Should not have
• The calendar should not use photographs or resemble standard or cheesy wall calendars. No watermarks please.

```html
<!DOCTYPE html>
<html lang="en">
<head>
<meta charset="utf-8">
<title>XYZ Co 2012 Planner</title>
<link rel="stylesheet" href="https://fonts.googleapis.com/css2?family=Nunito:wght@700;800;900&family=Varela+Round&display=swap">
<style>
  :root {
    --sky: #33b9ee;
    --sky-deep: #22aee6;
    --ink: #4a4a55;
    --white: #ffffff;
    --orange: #f7941d;
    --blue: #00aeef;
    --pink: #f06eaa;
    --red: #ed1c24;
    --green: #7cbb3c;
    --purple: #9b59a6;
    --tint-yellow: #fffbd0;
    --mark-yellow: #fff38c;
    --tint-blue: #e7f6fd;
    --mark-blue: #c6e9f9;
    --tint-pink: #fdf0f6;
    --mark-pink: #fbd6e7;
    --tint-peach: #fdeee0;
    --mark-peach: #fdd6b8;
    --tint-green: #eff6e6;
    --mark-green: #d8ebc3;
    --tint-lilac: #f6f2f8;
    --mark-lilac: #e6d9ec;
  }
  * { box-sizing: border-box; margin: 0; padding: 0; }
  html, body { width: 847px; height: 1200px; overflow: hidden; }
  body {
    background: linear-gradient(135deg, var(--sky) 0%, var(--sky-deep) 100%);
    font-family: "Varela Round", "Nunito", sans-serif;
    position: relative;
  }
  .planner {
    position: absolute;
    left: 31px;
    top: 0;
    display: flex;
    gap: 3.5px;
  }
  .month { width: 62px; }
  .month h2 {
    height: 79px;
    background: var(--hue);
    color: var(--white);
    font-family: "Nunito", sans-serif;
    font-weight: 800;
    font-size: 25px;
    letter-spacing: -0.5px;
    text-align: center;
    padding-top: 39px;
    line-height: 1;
  }
  .month ol {
    list-style: none;
    margin-top: 2.5px;
    display: flex;
    flex-direction: column;
    gap: 3.4px;
  }
  .month li {
    height: 30.05px;
    background: var(--tint);
    border: 1px solid rgba(255,255,255,0.85);
    border-radius: 5px;
    padding: 3px 0 0 4px;
    color: var(--ink);
    font-size: 7.5px;
    line-height: 1;
  }
  .month li b {
    display: block;
    font-weight: 400;
    font-size: 13px;
    line-height: 12px;
    margin-bottom: 1px;
  }
  .month li.weekend { background: var(--mark); color: var(--hue); }
  .jan { --hue: var(--orange); --tint: var(--tint-yellow); --mark: var(--mark-yellow); }
  .feb { --hue: var(--blue); --tint: var(--tint-blue); --mark: var(--mark-blue); }
  .mar { --hue: var(--pink); --tint: var(--tint-pink); --mark: var(--mark-pink); }
  .apr { --hue: var(--red); --tint: var(--tint-peach); --mark: var(--mark-peach); }
  .may { --hue: var(--green); --tint: var(--tint-green); --mark: var(--mark-green); }
  .jun { --hue: var(--purple); --tint: var(--tint-lilac); --mark: var(--mark-lilac); }
  .title {
    position: absolute;
    left: 31px;
    top: 1130px;
    color: var(--white);
    font-family: "Nunito", sans-serif;
    font-weight: 900;
    font-size: 46px;
    line-height: 1;
    letter-spacing: 0.5px;
  }
</style>
</head>
<body>
<main class="planner">
  <section class="month jan"><h2>JAN</h2><ol>
    <li class="weekend"><b>01</b>Sun</li><li><b>02</b>Mon</li><li><b>03</b>Tue</li><li><b>02</b>Thu</li><li><b>05</b>Thu</li><li><b>06</b>Fri</li><li class="weekend"><b>07</b>Sat</li>
    <li class="weekend"><b>08</b>Sun</li><li><b>09</b>Mon</li><li><b>10</b>Tue</li><li><b>02</b>Thu</li><li><b>12</b>Thu</li><li><b>13</b>Fri</li><li class="weekend"><b>14</b>Sat</li>
    <li class="weekend"><b>15</b>Sun</li><li><b>16</b>Mon</li><li><b>17</b>Tue</li><li><b>02</b>Thu</li><li><b>19</b>Thu</li><li><b>20</b>Fri</li><li class="weekend"><b>21</b>Sat</li>
    <li class="weekend"><b>22</b>Sun</li><li><b>23</b>Mon</li><li><b>24</b>Tue</li><li><b>02</b>Thu</li><li><b>26</b>Thu</li><li><b>27</b>Fri</li><li class="weekend"><b>28</b>Sat</li>
    <li class="weekend"><b>29</b>Sun</li><li><b>30</b>Mon</li><li><b>31</b>Tue</li>
  </ol></section>
  <section class="month feb"><h2>FEB</h2><ol>
    <li><b>01</b>Wed</li><li><b>02</b>Thu</li><li><b>01</b>Wed</li><li class="weekend"><b>02</b>Thu</li><li class="weekend"><b>01</b>Wed</li><li><b>02</b>Thu</li><li><b>01</b>Wed</li>
    <li><b>01</b>Wed</li><li><b>02</b>Thu</li><li><b>01</b>Wed</li><li class="weekend"><b>02</b>Thu</li><li class="weekend"><b>01</b>Wed</li><li><b>02</b>Thu</li><li><b>01</b>Wed</li>
    <li><b>01</b>Wed</li><li><b>02</b>Thu</li><li><b>01</b>Wed</li><li class="weekend"><b>02</b>Thu</li><li class="weekend"><b>01</b>Wed</li><li><b>02</b>Thu</li><li><b>01</b>Wed</li>
    <li><b>01</b>Wed</li><li><b>02</b>Thu</li><li><b>01</b>Wed</li><li class="weekend"><b>02</b>Thu</li><li class="weekend"><b>01</b>Wed</li><li><b>02</b>Thu</li><li><b>01</b>Wed</li>
    <li><b>01</b>Wed</li><li><b>02</b>Thu</li><li><b>01</b>Wed</li>
  </ol></section>
  <section class="month mar"><h2>MAR</h2><ol>
    <li><b>01</b>Thu</li><li><b>02</b>Fri</li><li class="weekend"><b>01</b>Thu</li><li class="weekend"><b>02</b>Fri</li><li><b>01</b>Thu</li><li><b>02</b>Fri</li><li><b>01</b>Thu</li>
    <li><b>01</b>Thu</li><li><b>02</b>Fri</li><li class="weekend"><b>01</b>Thu</li><li class="weekend"><b>02</b>Fri</li><li><b>01</b>Thu</li><li><b>02</b>Fri</li><li><b>01</b>Thu</li>
    <li><b>01</b>Thu</li><li><b>02</b>Fri</li><li class="weekend"><b>01</b>Thu</li><li class="weekend"><b>02</b>Fri</li><li><b>01</b>Thu</li><li><b>02</b>Fri</li><li><b>01</b>Thu</li>
    <li><b>01</b>Thu</li><li><b>02</b>Fri</li><li class="weekend"><b>01</b>Thu</li><li class="weekend"><b>02</b>Fri</li><li><b>01</b>Thu</li><li><b>02</b>Fri</li><li><b>01</b>Thu</li>
    <li><b>01</b>Thu</li><li><b>02</b>Fri</li><li class="weekend"><b>01</b>Thu</li>
  </ol></section>
  <section class="month apr"><h2>APR</h2><ol>
    <li><b>01</b>Sun</li><li><b>02</b>Mon</li><li><b>01</b>Sun</li><li><b>02</b>Mon</li><li><b>01</b>Sun</li><li><b>02</b>Mon</li><li class="weekend"><b>01</b>Sun</li>
    <li class="weekend"><b>01</b>Sun</li><li><b>02</b>Mon</li><li><b>01</b>Sun</li><li><b>02</b>Mon</li><li><b>01</b>Sun</li><li><b>02</b>Mon</li><li class="weekend"><b>01</b>Sun</li>
    <li class="weekend"><b>01</b>Sun</li><li><b>02</b>Mon</li><li><b>01</b>Sun</li><li><b>02</b>Mon</li><li><b>01</b>Sun</li><li><b>02</b>Mon</li><li class="weekend"><b>01</b>Sun</li>
    <li class="weekend"><b>01</b>Sun</li><li><b>02</b>Mon</li><li><b>01</b>Sun</li><li><b>02</b>Mon</li><li><b>01</b>Sun</li><li><b>02</b>Mon</li><li class="weekend"><b>01</b>Sun</li>
    <li class="weekend"><b>01</b>Sun</li><li><b>02</b>Mon</li><li><b>01</b>Sun</li>
  </ol></section>
  <section class="month may"><h2>MAY</h2><ol>
    <li><b>01</b>Tue</li><li><b>02</b>Wed</li><li><b>01</b>Tue</li><li><b>02</b>Wed</li><li class="weekend"><b>01</b>Tue</li><li class="weekend"><b>02</b>Wed</li><li><b>01</b>Tue</li>
    <li><b>01</b>Tue</li><li><b>02</b>Wed</li><li><b>01</b>Tue</li><li><b>02</b>Wed</li><li class="weekend"><b>01</b>Tue</li><li class="weekend"><b>02</b>Wed</li><li><b>01</b>Tue</li>
    <li><b>01</b>Tue</li><li><b>02</b>Wed</li><li><b>01</b>Tue</li><li><b>02</b>Wed</li><li class="weekend"><b>01</b>Tue</li><li class="weekend"><b>02</b>Wed</li><li><b>01</b>Tue</li>
    <li><b>01</b>Tue</li><li><b>02</b>Wed</li><li><b>01</b>Tue</li><li><b>02</b>Wed</li><li class="weekend"><b>01</b>Tue</li><li class="weekend"><b>02</b>Wed</li><li><b>01</b>Tue</li>
    <li><b>01</b>Tue</li><li><b>02</b>Wed</li><li><b>01</b>Tue</li>
  </ol></section>
  <section class="month jun"><h2>JUN</h2><ol>
    <li><b>01</b>Fri</li><li class="weekend"><b>02</b>Sat</li><li class="weekend"><b>01</b>Fri</li><li><b>02</b>Sat</li><li><b>01</b>Fri</li><li><b>02</b>Sat</li><li><b>01</b>Fri</li>
    <li><b>01</b>Fri</li><li class="weekend"><b>02</b>Sat</li><li class="weekend"><b>01</b>Fri</li><li><b>02</b>Sat</li><li><b>01</b>Fri</li><li><b>02</b>Sat</li><li><b>01</b>Fri</li>
    <li><b>01</b>Fri</li><li class="weekend"><b>02</b>Sat</li><li class="weekend"><b>01</b>Fri</li><li><b>02</b>Sat</li><li><b>01</b>Fri</li><li><b>02</b>Sat</li><li><b>01</b>Fri</li>
    <li><b>01</b>Fri</li><li class="weekend"><b>02</b>Sat</li><li class="weekend"><b>01</b>Fri</li><li><b>02</b>Sat</li><li><b>01</b>Fri</li><li><b>02</b>Sat</li><li><b>01</b>Fri</li>
    <li><b>01</b>Fri</li><li class="weekend"><b>02</b>Sat</li><li class="weekend"><b>01</b>Fri</li>
  </ol></section>
  <section class="month jan"><h2>JUL</h2><ol>
    <li class="weekend"><b>01</b>Sun</li><li><b>02</b>Mon</li><li><b>01</b>Sun</li><li><b>02</b>Mon</li><li><b>01</b>Sun</li><li><b>02</b>Mon</li><li class="weekend"><b>01</b>Sun</li>
    <li class="weekend"><b>01</b>Sun</li><li><b>02</b>Mon</li><li><b>01</b>Sun</li><li><b>02</b>Mon</li><li><b>01</b>Sun</li><li><b>02</b>Mon</li><li class="weekend"><b>01</b>Sun</li>
    <li class="weekend"><b>01</b>Sun</li><li><b>02</b>Mon</li><li><b>01</b>Sun</li><li><b>02</b>Mon</li><li><b>01</b>Sun</li><li><b>02</b>Mon</li><li class="weekend"><b>01</b>Sun</li>
    <li class="weekend"><b>01</b>Sun</li><li><b>02</b>Mon</li><li><b>01</b>Sun</li><li><b>02</b>Mon</li><li><b>01</b>Sun</li><li><b>02</b>Mon</li><li class="weekend"><b>01</b>Sun</li>
    <li class="weekend"><b>01</b>Sun</li><li><b>02</b>Mon</li><li><b>01</b>Sun</li>
  </ol></section>
  <section class="month feb"><h2>AUG</h2><ol>
    <li><b>01</b>Wed</li><li><b>02</b>Thu</li><li><b>01</b>Wed</li><li><b>02</b>Thu</li><li><b>01</b>Wed</li><li><b>02</b>Thu</li><li><b>01</b>Wed</li>
    <li><b>01</b>Wed</li><li><b>02</b>Thu</li><li><b>01</b>Wed</li><li><b>02</b>Thu</li><li><b>01</b>Wed</li><li><b>02</b>Thu</li><li><b>01</b>Wed</li>
    <li><b>01</b>Wed</li><li><b>02</b>Thu</li><li><b>01</b>Wed</li><li><b>02</b>Thu</li><li><b>01</b>Wed</li><li><b>02</b>Thu</li><li><b>01</b>Wed</li>
    <li><b>01</b>Wed</li><li><b>02</b>Thu</li><li><b>01</b>Wed</li><li><b>02</b>Thu</li><li><b>01</b>Wed</li><li><b>02</b>Thu</li><li><b>01</b>Wed</li>
    <li><b>01</b>Wed</li><li><b>02</b>Thu</li><li><b>01</b>Wed</li>
  </ol></section>
  <section class="month mar"><h2>SEP</h2><ol>
    <li><b>01</b>Sat</li><li><b>02</b>Sun</li><li><b>01</b>Sat</li><li><b>02</b>Sun</li><li><b>01</b>Sat</li><li><b>02</b>Sun</li><li><b>01</b>Sat</li>
    <li><b>01</b>Sat</li><li><b>02</b>Sun</li><li><b>01</b>Sat</li><li><b>02</b>Sun</li><li><b>01</b>Sat</li><li><b>02</b>Sun</li><li><b>01</b>Sat</li>
    <li><b>01</b>Sat</li><li><b>02</b>Sun</li><li><b>01</b>Sat</li><li><b>02</b>Sun</li><li><b>01</b>Sat</li><li><b>02</b>Sun</li><li><b>01</b>Sat</li>
    <li><b>01</b>Sat</li><li><b>02</b>Sun</li><li><b>01</b>Sat</li><li><b>02</b>Sun</li><li><b>01</b>Sat</li><li><b>02</b>Sun</li><li><b>01</b>Sat</li>
    <li><b>01</b>Sat</li><li><b>02</b>Sun</li><li><b>01</b>Sat</li>
  </ol></section>
  <section class="month apr"><h2>OCT</h2><ol>
    <li><b>01</b>Mon</li><li><b>02</b>Tue</li><li><b>01</b>Mon</li><li><b>02</b>Tue</li><li><b>01</b>Mon</li><li><b>02</b>Tue</li><li><b>01</b>Mon</li>
    <li><b>01</b>Mon</li><li><b>02</b>Tue</li><li><b>01</b>Mon</li><li><b>02</b>Tue</li><li><b>01</b>Mon</li><li><b>02</b>Tue</li><li><b>01</b>Mon</li>
    <li><b>01</b>Mon</li><li><b>02</b>Tue</li><li><b>01</b>Mon</li><li><b>02</b>Tue</li><li><b>01</b>Mon</li><li><b>02</b>Tue</li><li><b>01</b>Mon</li>
    <li><b>01</b>Mon</li><li><b>02</b>Tue</li><li><b>01</b>Mon</li><li><b>02</b>Tue</li><li><b>01</b>Mon</li><li><b>02</b>Tue</li><li><b>01</b>Mon</li>
    <li><b>01</b>Mon</li><li><b>02</b>Tue</li><li><b>01</b>Mon</li>
  </ol></section>
  <section class="month may"><h2>NOV</h2><ol>
    <li><b>01</b>Thu</li><li><b>02</b>Fri</li><li><b>01</b>Thu</li><li><b>02</b>Fri</li><li><b>01</b>Thu</li><li><b>02</b>Fri</li><li><b>01</b>Thu</li>
    <li><b>01</b>Thu</li><li><b>02</b>Fri</li><li><b>01</b>Thu</li><li><b>02</b>Fri</li><li><b>01</b>Thu</li><li><b>02</b>Fri</li><li><b>01</b>Thu</li>
    <li><b>01</b>Thu</li><li><b>02</b>Fri</li><li><b>01</b>Thu</li><li><b>02</b>Fri</li><li><b>01</b>Thu</li><li><b>02</b>Fri</li><li><b>01</b>Thu</li>
    <li><b>01</b>Thu</li><li><b>02</b>Fri</li><li><b>01</b>Thu</li><li><b>02</b>Fri</li><li><b>01</b>Thu</li><li><b>02</b>Fri</li><li><b>01</b>Thu</li>
    <li><b>01</b>Thu</li><li><b>02</b>Fri</li><li><b>01</b>Thu</li>
  </ol></section>
  <section class="month jun"><h2>DEC</h2><ol>
    <li><b>01</b>Sat</li><li><b>02</b>Sun</li><li><b>01</b>Sat</li><li><b>02</b>Sun</li><li><b>01</b>Sat</li><li><b>02</b>Sun</li><li><b>01</b>Sat</li>
    <li><b>01</b>Sat</li><li><b>02</b>Sun</li><li><b>01</b>Sat</li><li><b>02</b>Sun</li><li><b>01</b>Sat</li><li><b>02</b>Sun</li><li><b>01</b>Sat</li>
    <li><b>01</b>Sat</li><li><b>02</b>Sun</li><li><b>01</b>Sat</li><li><b>02</b>Sun</li><li><b>01</b>Sat</li><li><b>02</b>Sun</li><li><b>01</b>Sat</li>
    <li><b>01</b>Sat</li><li><b>02</b>Sun</li><li><b>01</b>Sat</li><li><b>02</b>Sun</li><li><b>01</b>Sat</li><li><b>02</b>Sun</li><li><b>01</b>Sat</li>
    <li><b>01</b>Sat</li><li><b>02</b>Sun</li><li><b>01</b>Sat</li>
  </ol></section>
</main>
<h1 class="title">XYZ CO 2012 PLANNER</h1>
</body>
</html>
```